Slogan
Zielgruppe
Wir sind ein Familienhotel in Österreich. Unsere Zielgruppe sind Familien und auch Paare. Unsere Hauptthemen sind im Sommer wandern und im Winter skifahren.
Aufgabenstellung
Es soll aus dem Claim hervorgehen, dass wir besonders Familien ansprechen. Wir sind jedoch kein reines Kinderhotel. Es sind bei uns auch Paare willkommen.

```html
<!DOCTYPE html>
<html lang="de">
<head>
<meta charset="utf-8">
<title>Slogan – Ein Traum für Familien und Paare</title>
<link rel="stylesheet" href="https://fonts.googleapis.com/css2?family=Arimo:wght@400&display=swap">
<style>
  :root {
    --canvas-bg: #ffffff;
    --slogan-blue: #0a8fc4;
  }
  html, body {
    margin: 0;
    padding: 0;
    overflow: hidden;
    background: var(--canvas-bg);
  }
  .canvas {
    width: 1200px;
    height: 1200px;
    background: var(--canvas-bg);
    display: flex;
    align-items: center;
    justify-content: center;
  }
  .slogan {
    margin: 0;
    margin-top: -4px;
    font-family: "Arimo", Arial, sans-serif;
    font-weight: 400;
    font-size: 55px;
    letter-spacing: 0;
    color: var(--slogan-blue);
    white-space: nowrap;
  }
</style>
</head>
<body>
  <main class="canvas">
    <p class="slogan">Ein Traum für Familien und Paare!</p>
  </main>
</body>
</html>
```